Boutique custom software development company needs new business card

Our nearly 20 year old custom software development company would like to better include the fact that we are now providing Bitcoin services. These new services are B2B include education (how to acquire and securely hold Bitcoin) and integrating Bitcoin payments into existing ecommerce sites or other existing systems. Please keep the card clean and simple. Attached is our current design and some other files. vextorial.com

Target Market(s)

businesses owners interested in long term relationship

Industry/Entity Type

Custom software development and Bitcoin

Contact Information for Business Card

Dale Parker, dale@vextorial.com, vextorial.com, (888) 555-VXTRL

Font styles to use
Other font styles liked:
• monospace

Requirements
Must have
• double-sided
Nice to have
• clean and simple
Should not have
• physical address

```html
<!DOCTYPE html>
<html lang="en">
<head>
<meta charset="utf-8">
<title>Vextorial – Business Card</title>
<link rel="stylesheet" href="https://fonts.googleapis.com/css2?family=Roboto+Mono:wght@400;700&family=Lato:wght@400;900&display=swap">
<style>
  :root {
    --backdrop: #e9e4dc;
    --card-white: #ffffff;
    --card-navy: #131a45;
    --brand-blue: #3d72b9;
    --brand-orange: #ee7d22;
    --ink: #2b2b2b;
  }
  * { margin: 0; padding: 0; box-sizing: border-box; }
  html, body { width: 900px; height: 1200px; overflow: hidden; }
  body {
    background: var(--backdrop);
    position: relative;
    font-family: "Roboto Mono", monospace;
  }
  .card {
    position: absolute;
    left: 78px;
    width: 744px;
    border-radius: 32px;
    box-shadow: 0 4px 10px rgba(0,0,0,0.25);
  }
  .card-front { top: 130px; height: 442px; background: var(--card-white); }
  .card-back { top: 638px; height: 440px; background: var(--card-navy); }

  .brand-block {
    position: absolute;
    left: 67px; top: 78px;
    width: 276px; height: 287px;
    display: flex; align-items: center; justify-content: center; gap: 12px;
  }
  .brand-square { width: 22px; height: 22px; background: var(--brand-orange); }
  .brand-name {
    font-family: "Roboto Mono", monospace;
    font-weight: 700;
    font-size: 38px;
    color: var(--brand-blue);
    letter-spacing: -0.5px;
  }
  .divider {
    position: absolute;
    left: 376px; top: 78px;
    width: 2px; height: 287px;
    background: var(--brand-orange);
  }
  .contact { position: absolute; left: 407px; top: 98px; color: var(--ink); }
  .person-name {
    font-weight: 700; font-size: 27px; color: var(--brand-orange);
    letter-spacing: 0.5px; line-height: 1.2;
  }
  .person-title { font-size: 16px; margin-top: 4px; letter-spacing: 0.3px; }
  .contact-list { list-style: none; margin-top: 28px; font-size: 16px; }
  .contact-list li { display: flex; align-items: center; gap: 6px; height: 25px; }
  .contact-list svg { width: 16px; height: 16px; fill: var(--brand-orange); }
  .services { margin-top: 34px; font-size: 16px; line-height: 25px; }

  .back-name {
    position: absolute; left: 0; right: 0; top: 124px;
    text-align: center;
    font-family: "Lato", sans-serif; font-weight: 900;
    font-size: 114px; line-height: 1; letter-spacing: 2px;
    color: var(--brand-blue);
  }
  .tagline {
    position: absolute; left: 0; right: 0; top: 272px;
    text-align: center;
    font-family: "Lato", sans-serif; font-weight: 400;
    font-size: 40px; letter-spacing: -1px;
    color: var(--brand-blue);
  }
</style>
</head>
<body>
  <section class="card card-front">
    <div class="brand-block">
      <span class="brand-square"></span>
      <span class="brand-name">vextorial</span>
    </div>
    <div class="divider"></div>
    <div class="contact">
      <p class="person-name">Dale Parker</p>
      <p class="person-title">Founding Partner</p>
      <ul class="contact-list">
        <li><svg viewBox="0 0 16 16" aria-hidden="true"><path d="M2 6c0-2 2-3 6-3s6 1 6 3v1h-3V5.5H5V7H2z M4 8h8l2 5H2z"/></svg>(888) 555-VXTRL</li>
        <li><svg viewBox="0 0 16 16" aria-hidden="true"><path d="M1 3h14v1.5L8 9 1 4.5z M1 6.3 8 11l7-4.7V13H1z"/></svg>dale@vextorial.com</li>
        <li><svg viewBox="0 0 16 16" aria-hidden="true"><circle cx="8" cy="8" r="7"/><path d="M5 4c2 1 1 3 3 3s1 3 0 4" stroke="#fff" stroke-width="1.3" fill="none"/></svg>www.vextorial.com</li>
      </ul>
      <p class="services">Custom Software &amp;<br>Bitcoin B2B Services</p>
    </div>
  </section>

  <section class="card card-back">
    <p class="back-name">VEXTORIAL</p>
    <p class="tagline">custom applications &amp; bitcoin services</p>
  </section>
</body>
</html>
```